KRT Flyer to attract applicants 11x17

Lantern Stagehand Collective provides crew for local concerts, filming, theater, and corporate events.
The flyer will be posted on bulletin boards at colleges with theater programs.
Our primary venues are historic theaters in downtown LA
Need a 11x17 poster to attract potential applicants/crew
I have attached a poster that one of our staff made that has all if the relevant info - but i know the poster can look much better than that. I have also attached many images and our logo. It is not necessary to use all of the images, or any of them. The two images of the theater interiors are the venues we operate so they would be the first to include. I can send additional info or images upon request. Thank you

Industry/Entity Type

Entertainment

Requirements
Must have
• APPLY@KRTCREW.EXAMPLE

```html
<!DOCTYPE html>
<html lang="en">
<head>
<meta charset="utf-8">
<title>KRT – Open Positions</title>
<link rel="stylesheet" href="https://fonts.googleapis.com/css2?family=Montserrat:wght@400;700;800&family=Great+Vibes&display=swap">
<style>
  :root {
    --page-bg: #2e3187;
    --poster-night: #15103a;
    --poster-violet: #3a1f78;
    --city-magenta: #8a2a8c;
    --city-blue: #3b3aa0;
    --stage-purple: #6a3aa8;
    --stage-pink: #c2489e;
    --glow-pink: #ff3fb4;
    --text-white: #ffffff;
    --text-soft: #ecebf6;
  }
  * { box-sizing: border-box; margin: 0; padding: 0; }
  html, body { width: 1200px; height: 1200px; overflow: hidden; }
  body { background: var(--page-bg); position: relative; font-family: "Montserrat", Arial, sans-serif; }

  .poster {
    position: absolute; left: 236px; top: 40px; width: 704px; height: 1087px;
    background: linear-gradient(180deg, var(--poster-night) 0%, #1f1552 30%, var(--poster-violet) 60%, #4a2a8e 100%);
    overflow: hidden;
    box-shadow: 4px 6px 12px rgba(0,0,0,.35);
  }
  .city-photo {
    position: absolute; left: 0; top: 250px; width: 100%; height: 500px;
    background:
      radial-gradient(ellipse at 30% 60%, rgba(210,70,170,.55), transparent 60%),
      radial-gradient(ellipse at 75% 55%, rgba(90,90,200,.55), transparent 60%),
      linear-gradient(180deg, transparent 0%, var(--city-magenta) 45%, var(--city-blue) 80%, transparent 100%);
    opacity: .85;
  }
  .stage-photo {
    position: absolute; left: 0; bottom: 0; width: 100%; height: 330px;
    background:
      radial-gradient(ellipse at 15% 45%, rgba(240,200,255,.55), transparent 45%),
      radial-gradient(ellipse at 40% 95%, rgba(220,70,160,.6), transparent 50%),
      linear-gradient(180deg, rgba(80,40,150,0) 0%, var(--stage-purple) 35%, var(--stage-pink) 100%);
  }

  .brand-mark {
    position: absolute; left: 0; top: 70px; width: 100%;
    display: flex; align-items: center; justify-content: center; gap: 22px;
  }
  .brand-mark svg { display: block; }
  .brand-mark .brand-initials {
    color: var(--text-white); font-weight: 700; font-size: 110px; letter-spacing: 6px; line-height: 1;
  }

  .company-name { position: absolute; left: 0; top: 272px; width: 100%; text-align: center; color: var(--text-white); font-weight: 700; }
  .company-name .line-main { font-size: 40px; letter-spacing: 1px; line-height: 1.1; }
  .company-name .line-sub {
    display: flex; align-items: center; justify-content: center; gap: 14px;
    font-size: 24px; letter-spacing: 18px; margin-top: 8px;
  }
  .company-name .rule { width: 100px; height: 3px; background: var(--text-white); }

  .headline {
    position: absolute; left: 0; top: 400px; width: 100%; text-align: center;
    color: var(--text-white); font-weight: 800; font-size: 80px; line-height: .98;
    text-shadow: 0 0 10px var(--glow-pink), 0 0 22px var(--glow-pink);
  }

  .pitch {
    position: absolute; left: 10px; top: 645px; width: 684px; text-align: center;
    color: var(--text-soft); font-weight: 700; font-size: 25px; line-height: 1.42; letter-spacing: 1px;
    transform: rotate(-1.8deg);
    text-shadow: 2px 3px 2px rgba(20,10,50,.8);
  }

  .cta-script {
    position: absolute; left: 0; top: 780px; width: 100%; text-align: center;
    font-family: "Great Vibes", cursive; font-size: 46px; color: var(--text-white);
    text-shadow: 0 0 8px var(--glow-pink);
  }
  .apply-email {
    position: absolute; left: 0; top: 868px; width: 100%; text-align: center;
    color: var(--text-white); font-weight: 700; font-size: 34px; letter-spacing: 1px;
  }
  .website {
    position: absolute; left: 0; top: 1040px; width: 100%; text-align: center;
    color: var(--text-white); font-weight: 400; font-size: 26px; letter-spacing: 4px;
  }
</style>
</head>
<body>
  <main class="poster">
    <div class="city-photo" role="img" aria-label="Night skyline of downtown Los Angeles in magenta and blue light"></div>
    <div class="stage-photo" role="img" aria-label="Historic theater interior with stage lights and seating"></div>

    <div class="brand-mark">
      <svg width="90" height="90" viewBox="0 0 90 90" aria-hidden="true">
        <circle cx="45" cy="45" r="38" fill="none" stroke="#ffffff" stroke-width="10"/>
      </svg>
      <span class="brand-initials">KRT</span>
    </div>

    <div class="company-name">
      <div class="line-main">LANTERN STAGEHAND</div>
      <div class="line-sub"><span class="rule"></span>COLLECTIVE<span class="rule"></span></div>
    </div>

    <h1 class="headline">HAS OPEN<br>POSITIONS</h1>

    <p class="pitch">WE ARE LOOKING FOR TELENTED<br>TECHNICIANS TO ADD TO OUR ROSTER<br>OF SKILLED PROFESSIONALS.</p>

    <p class="cta-script">Send Resume To</p>
    <p class="apply-email">APPLY@KRTCREW.EXAMPLE</p>
    <p class="website">WWW.KRTCREW.EXAMPLE</p>
  </main>
</body>
</html>
```